Silver Meadow LLC business card

I help with the Marketing and Sales of various Natural, Organic, Eco Friendly and Healthy Main Stream products to Retail Corporate accounts as well as Independents and Distributors.I also highlight Private label items to these same Retail Corporate accounts.Cherish the Moments, Enjoy Life!

Speciality & Health Sales and Marketing

Target Market(s)

Men and Women

Industry/Entity Type

Business

Contact Information for Business Card

Silver Meadow, LLC
Janet Louise Verhagen
438 West Finch Lane
Ste 4-237
Phoenix, AZ 85047
602-555-0147
jverhagen@plumvale.net

Requirements
Must have
• Nice, femine font
Something in the background or on a side with a softness
Nice to have
• Cherish the Moments, Enjoy Life
Should not have
• Hardness

```html
<!DOCTYPE html>
<html lang="en">
<head>
<meta charset="utf-8">
<title>Silver Meadow LLC – Business Card</title>
<link href="https://fonts.googleapis.com/css2?family=Josefin+Sans:wght@300;400;600&display=swap" rel="stylesheet">
<style>
  :root {
    --backdrop: #2d2b2c;
    --card: #232122;
    --card-glow: #35302f;
    --card-edge: #3a3536;
    --ink: #f4f0ee;
    --ink-soft: #d9d2cf;
    --mark-soft: #8c8487;
    --rule: #4a4344;
  }
  * { margin: 0; padding: 0; box-sizing: border-box; }
  html, body { width: 1200px; height: 900px; overflow: hidden; }
  body {
    background: var(--backdrop);
    font-family: "Josefin Sans", sans-serif;
    color: var(--ink);
    position: relative;
  }
  .card {
    position: absolute;
    top: 300px;
    width: 520px;
    height: 300px;
    border-radius: 28px;
    border: 1px solid var(--card-edge);
    background:
      radial-gradient(circle at 22% 50%, var(--card-glow) 0%, var(--card) 60%);
    box-shadow: 0 18px 40px rgba(0, 0, 0, 0.35);
  }
  .card--back { left: 60px; }
  .card--front {
    left: 620px;
    background:
      radial-gradient(ellipse at 50% 45%, var(--card-glow) 0%, var(--card) 70%);
  }

  .brand-square {
    background: var(--mark-soft);
    border-radius: 18px;
  }
  .brand-name {
    font-weight: 300;
    color: var(--ink);
    letter-spacing: 1px;
    white-space: nowrap;
  }

  /* back side */
  .back-brand {
    position: absolute;
    left: 28px;
    top: 0;
    width: 200px;
    height: 100%;
    display: flex;
    flex-direction: column;
    align-items: center;
    justify-content: center;
    gap: 18px;
  }
  .back-brand .brand-square { width: 104px; height: 90px; }
  .back-brand .brand-name { font-size: 19px; }

  .back-divider {
    position: absolute;
    left: 246px;
    top: 40px;
    width: 1px;
    height: 220px;
    background: var(--rule);
  }
  .contact {
    position: absolute;
    left: 268px;
    right: 20px;
    top: 62px;
    font-size: 14px;
    font-weight: 300;
    line-height: 1.45;
    color: var(--ink-soft);
  }
  .contact .person-name {
    font-size: 19px;
    font-weight: 600;
    color: var(--ink);
    line-height: 1.15;
    white-space: nowrap;
  }
  .contact .person-role { font-size: 13px; margin-bottom: 14px; }
  .contact .address { margin-bottom: 12px; }

  /* front side */
  .front-brand {
    position: absolute;
    inset: 0;
    display: flex;
    flex-direction: column;
    align-items: center;
    justify-content: center;
    gap: 24px;
  }
  .front-brand .brand-square { width: 88px; height: 70px; border-radius: 16px; }
  .front-brand .brand-name { font-size: 36px; }
</style>
</head>
<body>
  <section class="card card--back">
    <div class="back-brand">
      <div class="brand-square"></div>
      <span class="brand-name">Silver Meadow LLC</span>
    </div>
    <div class="back-divider"></div>
    <div class="contact">
      <p class="person-name">Janet Louise Verhagen</p>
      <p class="person-role">Managing Director</p>
      <p class="address">438 West Finch Lane, Ste 4-237<br>Phoenix, AZ 85047</p>
      <p>T: 602-555-0147<br>E: jverhagen@plumvale.net<br>W: www.plumvale.net</p>
    </div>
  </section>

  <section class="card card--front">
    <div class="front-brand">
      <div class="brand-square"></div>
      <span class="brand-name">Silver Meadow LLC</span>
    </div>
  </section>
</body>
</html>
```